Therapy and counselling practice needs a compelling double-sided promotional flyer

We need someone to design a highly engaging, easy to read, revenue generating promotional flyer that we can give to potential new clients. I have attached the content I need you to include, as well as the professional photo of myself and the company logo. Please use a colour scheme which matches the colours used in my logo. Our website is www.velmaro.com.au for reference to our practice. Need something that looks really modern and eye catching and positions the content in a way which isn't just like a jazzed up Word document.

Please also feel free to use additional images as you deem appropriate, relating to therapy / counselling with clients. See my website for examples - velmaro.com.au

```html
<!DOCTYPE html>
<html lang="en">
<head>
<meta charset="utf-8">
<title>Velmaro Health Services – Counselling Flyer</title>
<link href="https://fonts.googleapis.com/css2?family=League+Spartan:wght@700;800&family=Jost:wght@400;500;600&display=swap" rel="stylesheet">
<style>
  :root{
    --backdrop:#999999;
    --paper:#ffffff;
    --red:#dc1f26;
    --yellow:#fdd600;
    --black:#111111;
    --ink:#1b1b1b;
    --photo-a:#d9c9b6;
    --photo-b:#3b4251;
  }
  *{margin:0;padding:0;box-sizing:border-box}
  html,body{width:1200px;height:1200px;overflow:hidden;background:var(--backdrop)}
  body{position:relative;font-family:"Jost",sans-serif;color:var(--ink)}
  .page{position:absolute;top:272px;width:464px;height:655px;background:var(--paper);overflow:hidden}
  .page--front{left:106px}
  .page--back{left:647px}
  .abs{position:absolute}

  /* front */
  .corner{position:absolute;left:0;top:0}
  .brand-name{left:12px;top:46px;font-family:"Jost",sans-serif;font-weight:600;font-size:30px;letter-spacing:-0.5px;color:var(--black);line-height:1}
  .hero-band{left:0;top:121px;width:464px;height:219px;background:var(--yellow)}
  .hero-title{left:12px;top:137px;font-family:"League Spartan",sans-serif;font-weight:800;color:var(--red);font-size:22px;line-height:22.7px}
  .hero-copy{left:12px;top:216px;width:208px;font-size:11.2px;line-height:12.5px;color:var(--black)}
  .house{left:0;top:0}
  .why-band{left:0;top:346px;width:464px;height:124px;background:var(--red);padding:8px 12px 0}
  .why-title{font-family:"League Spartan",sans-serif;font-weight:800;color:var(--yellow);font-size:22px;line-height:24px}
  .why-sub{color:var(--yellow);font-size:21px;line-height:24px;font-weight:400}
  .why-copy{color:#fff;font-size:11px;line-height:14.3px;margin-top:7px;width:430px}
  .bullets{list-style:none}
  .bullets li{position:relative;padding-left:15px}
  .bullets li::before{content:"";position:absolute;left:0;top:5px;width:6px;height:6px;border-radius:50%;background:var(--red)}
  .front-list{left:12px;top:488px;width:420px;font-size:11px;line-height:14.3px}
  .front-list li{margin-bottom:8px}
  .front-list li::before{top:7px}
  .front-note{left:12px;top:564px;width:436px;font-size:11px;line-height:14.3px}
  .footer{left:0;bottom:0;width:464px;height:49px;background:var(--red);display:flex;align-items:center;justify-content:center;gap:9px;color:var(--yellow);font-size:18.5px;letter-spacing:.4px}
  .footer svg{display:block}
  .footer .contact{display:flex;align-items:center;gap:5px}

  /* back */
  .tab{left:0;height:37px;background:var(--yellow);padding-left:13px;display:flex;align-items:center;font-family:"League Spartan",sans-serif;font-weight:800;font-size:21.5px;color:var(--red);letter-spacing:.2px;white-space:nowrap}
  .back-text{left:12px;width:440px;font-size:11px;line-height:14.3px}
  .lead{font-family:"League Spartan",sans-serif;font-weight:700;font-size:11px}
  .subhead{font-weight:600}
  .back-list li::before{left:0;top:4.5px;width:5.5px;height:5.5px}
  .back-list li{padding-left:11px}
  .tech strong{color:var(--red);font-weight:600}
  .two-col{display:grid;grid-template-columns:206px 230px;column-gap:2px;width:450px}
</style>
</head>
<body>

<section class="page page--front" aria-label="Flyer front">
  <svg class="corner" width="464" height="200" viewBox="0 0 464 200">
    <polygon points="325,0 464,0 464,122" fill="var(--black)"/>
  </svg>

  <div class="brand-name abs">Velmaro</div>

  <div class="hero-band abs"></div>

  <svg class="house abs" width="464" height="346" viewBox="0 0 464 346">
    <defs>
      <linearGradient id="photoTone" x1="0" y1="0" x2="0" y2="1">
        <stop offset="0" stop-color="var(--photo-a)" stop-opacity="0"/>
        <stop offset="0.25" stop-color="var(--photo-a)"/>
        <stop offset="0.45" stop-color="var(--photo-b)"/>
        <stop offset="1" stop-color="var(--photo-b)"/>
      </linearGradient>
    </defs>
    <path d="M240 340 V152 Q240 140 248 131 L330 45 Q338 37 346 45 L428 131 Q436 140 436 152 V340 Z" fill="var(--paper)"/>
    <rect x="240" y="121" width="196" height="219" fill="var(--yellow)"/>
    <rect x="229" y="76" width="217" height="264" fill="url(#photoTone)" role="img" aria-label="Portrait photo of the counsellor in a navy suit, smiling"/>
    <path d="M240 318 V152 Q240 140 248 131 L330 45 Q338 37 346 45 L428 131 Q436 140 436 152 V318" fill="none" stroke="var(--red)" stroke-width="20" stroke-linejoin="round"/>
  </svg>

  <h1 class="hero-title abs">Reclaim Your<br>Well-Being with<br>Expert Counselling</h1>
  <p class="hero-copy abs">Life’s challenges and traumas can sometimes feel overwhelming. At Velmaro Health Services,we believe in your potential to overcome obstacles and lead a meaningful, fulfilling life. As a highly qualified therapist and counsellor, my name is Marcus Hollen, and I’m here to support you on your journey every step of the way.</p>

  <div class="why-band abs">
    <h2 class="why-title">Why Choose Me as Your Therapist?</h2>
    <h3 class="why-sub">Comprehensive Expertise</h3>
    <p class="why-copy">I bring a unique combination of skills and experience to my counselling practice, blending years of corporate leadership with a deep understanding of mental health.<br>My background includes:</p>
  </div>

  <ul class="bullets front-list abs">
    <li>Over a decade in corporate roles, specialising in leadership development, workplace culture, and HR strategy.</li>
    <li>Consulting experience with small to medium-sized enterprises, focusing on leadership coaching and employee engagement.</li>
  </ul>
  <p class="front-note abs">This foundation allows me to offer unique insights into the challenges faced by professionals and leaders, including work-related stress, burnout, and interpersonal dynamics.</p>

  <footer class="footer abs">
    <span class="contact">
      <svg width="15" height="15" viewBox="0 0 24 24"><path fill="var(--yellow)" d="M6.6 10.8a15.1 15.1 0 0 0 6.6 6.6l2.2-2.2c.3-.3.7-.4 1-.2 1.1.4 2.3.6 3.6.6.6 0 1 .4 1 1V20c0 .6-.4 1-1 1C10.6 21 3 13.4 3 4c0-.6.4-1 1-1h3.5c.6 0 1 .4 1 1 0 1.3.2 2.5.6 3.6.1.3 0 .7-.2 1z"/></svg>
      (03) 9412 5580
    </span>
    <span class="contact">
      <svg width="17" height="17" viewBox="0 0 24 24" fill="none" stroke="var(--yellow)" stroke-width="1.6"><circle cx="12" cy="12" r="10"/><ellipse cx="12" cy="12" rx="4.5" ry="10"/><path d="M2 12h20M4 7h16M4 17h16"/></svg>
      www.velmaro.com.au
    </span>
  </footer>
</section>

<section class="page page--back" aria-label="Flyer back">
  <h2 class="tab abs" style="top:12px;width:260px">Extensive Qualifications</h2>

  <p class="back-text lead abs" style="top:58px">I bring a solid foundation of academic and professional experience, including:</p>
  <ul class="bullets back-list back-text abs" style="top:77px">
    <li>Diploma of Counselling (Southern Institute of Applied Counselling).</li>
    <li>Certified Adolescent Counsellor (Carrington University).</li>
    <li>Postgraduate qualifications in Human Resource Management.</li>
  </ul>
  <p class="back-text subhead abs" style="top:128px">Specialised Therapeutic Techniques</p>
  <p class="back-text abs" style="top:150px;left:10px">At Velmaro Health Services, I use evidence-based approaches tailored to your individual needs:</p>
  <ul class="bullets back-list tech back-text abs" style="top:174px;width:405px">
    <li><strong>Cognitive Behavioural Therapy (CBT):</strong> Helping you identify and reframe unhelpful thought patterns.</li>
  </ul>
  <ul class="bullets back-list tech back-text abs" style="top:206px;width:380px">
    <li><strong>Acceptance and Commitment Therapy (ACT):</strong> Supporting you to embrace challenges while staying committed to your values</li>
  </ul>
  <ul class="bullets back-list tech back-text abs" style="top:242px;width:405px">
    <li><strong>Motivational Questioning:</strong> Encouraging meaningful change by exploring your strengths and aspirations.</li>
  </ul>

  <h2 class="tab abs" style="top:286px;width:260px">Trauma-Informed Care</h2>

  <p class="back-text abs" style="top:333px">As a trauma-informed counsellor, I understand the profound impact that trauma can have on mental, emotional, and physical well-being. Trauma-informed care means recognising the prevalence of trauma, understanding its effects, and creating a safe, supportive environment for healing.</p>
  <p class="back-text abs" style="top:395px">This approach benefits clients by:</p>
  <ul class="bullets back-list back-text abs" style="top:418px;width:420px">
    <li>Ensuring that therapy is sensitive to past experiences and avoids re-traumatisation.</li>
    <li>Helping clients build trust and safety in the therapeutic relationship.</li>
    <li>Empowering individuals to regain control, develop resilience, and move forward with confidence.</li>
  </ul>
  <p class="back-text abs" style="top:481px;width:418px">Whether you’re dealing with childhood trauma, grief, or life-altering events, I’m here to help you navigate your journey towards healing and recovery.</p>

  <h2 class="tab abs" style="top:525px;width:337px;padding-left:12px">A Unique Counselling Approach</h2>

  <ul class="bullets back-list two-col back-text abs" style="top:569px">
    <li>Navigate and heal from trauma.</li>
    <li>Improve relationships and communication.</li>
    <li>Develop resilience and coping strategies.</li>
    <li>Achieve personal growth and fulfilment.</li>
  </ul>

  <footer class="footer abs">
    <span class="contact">
      <svg width="15" height="15" viewBox="0 0 24 24"><path fill="var(--yellow)" d="M6.6 10.8a15.1 15.1 0 0 0 6.6 6.6l2.2-2.2c.3-.3.7-.4 1-.2 1.1.4 2.3.6 3.6.6.6 0 1 .4 1 1V20c0 .6-.4 1-1 1C10.6 21 3 13.4 3 4c0-.6.4-1 1-1h3.5c.6 0 1 .4 1 1 0 1.3.2 2.5.6 3.6.1.3 0 .7-.2 1z"/></svg>
      (03) 9412 5580
    </span>
    <span class="contact">
      <svg width="17" height="17" viewBox="0 0 24 24" fill="none" stroke="var(--yellow)" stroke-width="1.6"><circle cx="12" cy="12" r="10"/><ellipse cx="12" cy="12" rx="4.5" ry="10"/><path d="M2 12h20M4 7h16M4 17h16"/></svg>
      www.velmaro.com.au
    </span>
  </footer>
</section>

</body>
</html>
```